Harbor Bath & Steam Digital Billboard

This is a digital billboard so we are looking for a fresh design that will capture people's attention. The current billboard is a simple black text "#GottaSteam" over a white background with a picture of an vexaphone with one of our photos (Reference attached) We enjoy how clean and simple this design is, but open to other concepts. Since the weather is getting colder, a lot of people come to our spa because we offer various dry saunas and hot baths in addition to our spa services. We have a few photos for reference on our website information view www.harborbathsteam.example , but you can email me for additional photo content - otto@harborbathsteam.example

Target Market(s)

New Jersey Locals

Colors
0255a3
ec1f27
f37122
ffc214

Requirements
Must have
• Font is "Barlow"
Nice to have
• #GottaSteam hashtag

```html
<!DOCTYPE html>
<html lang="en">
<head>
<meta charset="utf-8">
<title>Harbor Bath &amp; Steam Billboard</title>
<link rel="stylesheet" href="https://fonts.googleapis.com/css2?family=Barlow:wght@500;600;800&display=swap">
<style>
  :root {
    --stage: #1b1b1b;
    --paper: #ffffff;
    --teal: #6ccbd4;
    --gold: #ffc214;
    --navy: #0255a3;
    --ink: #1a1a1a;
    --photo-light: #f6eee8;
    --photo-warm: #eccbb4;
  }
  * { margin: 0; padding: 0; box-sizing: border-box; }
  html, body { width: 1200px; height: 1200px; overflow: hidden; }
  body { background: var(--stage); position: relative; font-family: "Barlow", sans-serif; }

  .billboard {
    position: absolute;
    left: 30px; top: 434px;
    width: 1140px; height: 332px;
    background: var(--paper);
    overflow: hidden;
  }
  .footer-band {
    position: absolute;
    left: 0; bottom: 0;
    width: 100%; height: 73px;
    background: var(--navy);
  }
  .headline {
    position: absolute;
    left: 36px; top: 14px;
    font-weight: 800;
    font-size: 122px;
    line-height: 1;
    letter-spacing: -2px;
    white-space: nowrap;
  }
  .headline .lead { color: var(--teal); }
  .headline .accent { color: var(--gold); }

  .brand {
    position: absolute;
    left: 265px; top: 150px;
    width: 240px;
    text-align: center;
  }
  .brand-dot {
    display: block;
    width: 30px; height: 30px;
    margin: 0 auto 12px;
    border-radius: 50%;
    background: var(--teal);
  }
  .brand-name {
    font-weight: 600;
    font-size: 24px;
    line-height: 1.1;
    color: var(--ink);
    letter-spacing: 0.5px;
  }

  .web-address {
    position: absolute;
    left: 42px; bottom: 30px;
    color: var(--paper);
    font-weight: 500;
    font-size: 27px;
    line-height: 1;
    letter-spacing: 2px;
    white-space: nowrap;
  }

  .photo {
    position: absolute;
    right: 0; top: 0;
    width: 350px; height: 332px;
    background: linear-gradient(160deg, var(--photo-light) 0%, var(--photo-warm) 100%);
  }
</style>
</head>
<body>
  <section class="billboard">
    <div class="footer-band"></div>

    <div class="photo" role="img" aria-label="Photo of a woman in white sitting with bare legs outstretched, relaxing after a sauna"></div>

    <h1 class="headline"><span class="lead">#Gotta</span><span class="accent">Steam</span></h1>

    <div class="brand">
      <span class="brand-dot"></span>
      <p class="brand-name">Harbor Bath &amp; Steam</p>
    </div>

    <p class="web-address">www.harborbathsteam.example</p>
  </section>
</body>
</html>
```